QVR business card

Need a business card for a company that provides instructional design and elearning development services. The website is here: http://quorvane.studio/

I'm attaching a current logo, as well as the old business card design. While I like to keep it clean, the old design is too simplistic for my liking. The only idea I want to reuse from the old design is placing industry jargon on the back of the card, just need a better way to present it. But if you have other ideas for the back--feel free to experiment.

Please use the colors complementary to the color we have on the website. Thank you!

```html
<!DOCTYPE html>
<html lang="en">
<head>
<meta charset="utf-8">
<title>QVR business card</title>
<link rel="stylesheet" href="https://fonts.googleapis.com/css2?family=Montserrat:wght@400;600;700&family=Oswald:wght@400;500&display=swap">
<style>
  :root {
    --backdrop: #e9e6e1;
    --card: #ffffff;
    --ink: #3b3b3b;
    --ink-soft: #555555;
    --gold: #d8c98b;
    --gold-soft: #e6dcae;
    --teal: #1fb3a3;
    --line: #8a8a8a;
  }
  * { box-sizing: border-box; margin: 0; padding: 0; }
  html, body { width: 1200px; height: 1120px; overflow: hidden; }
  body {
    background: var(--backdrop);
    position: relative;
    font-family: "Montserrat", Arial, sans-serif;
    color: var(--ink);
  }
  .card {
    position: absolute;
    left: 150px;
    width: 900px;
    height: 514px;
    background: var(--card);
    box-shadow: 0 6px 18px rgba(0,0,0,0.18);
    overflow: hidden;
  }
  .card--front { top: 30px; }
  .card--back { top: 576px; }

  /* front */
  .corner-accent {
    position: absolute; top: 0; right: 0;
    width: 480px; height: 250px;
    background: linear-gradient(200deg, var(--gold) 0%, var(--gold-soft) 100%);
    clip-path: polygon(0 0, 100% 0, 100% 100%);
  }
  .holder { position: absolute; top: 26px; right: 36px; text-align: right; }
  .holder__name { font-weight: 700; font-size: 21px; color: var(--ink); }
  .holder__role { font-size: 18px; color: var(--ink-soft); margin-top: 4px; }
  .brand {
    position: absolute; left: 60px; top: 165px;
    display: flex; align-items: center; gap: 22px;
  }
  .brand__mark { width: 64px; height: 64px; background: var(--teal); }
  .brand__name {
    font-weight: 700; font-size: 88px; line-height: 1;
    color: var(--gold); letter-spacing: 2px;
  }
  .contacts {
    position: absolute; left: 60px; bottom: 48px;
    list-style: none; font-size: 19px; color: var(--ink);
  }
  .contacts li { display: flex; align-items: center; gap: 12px; margin-top: 10px; }
  .contacts svg { width: 18px; height: 18px; flex: none; }

  /* back */
  .headline {
    position: absolute; left: 48px; top: 30px;
    font-family: "Oswald", "Arial Narrow", sans-serif;
    font-weight: 400; font-size: 112px; line-height: 1.02;
    color: var(--ink); text-transform: uppercase;
  }
  .services {
    position: absolute; left: 320px; top: 38px;
    list-style: none;
  }
  .services__spine {
    position: absolute; left: 363px; top: 70px;
    width: 1px; height: 360px; background: var(--line);
  }
  .service {
    display: flex; align-items: center; gap: 22px;
    height: 74px;
  }
  .service__badge { width: 84px; height: 42px; flex: none; }
  .service__label {
    font-family: "Oswald", "Arial Narrow", sans-serif;
    font-weight: 500; font-size: 36px; letter-spacing: 0.5px;
    color: var(--ink); text-transform: uppercase; white-space: nowrap;
  }
</style>
</head>
<body>

<section class="card card--front" aria-label="Card front">
  <div class="corner-accent" role="img" aria-label="Decorative corner accent in gold and teal tones"></div>

  <div class="holder">
    <p class="holder__name">Marek Dovlatin</p>
    <p class="holder__role">Managing Director</p>
  </div>

  <div class="brand">
    <span class="brand__mark" aria-hidden="true"></span>
    <span class="brand__name">QVR</span>
  </div>

  <ul class="contacts">
    <li>
      <svg viewBox="0 0 20 20" aria-hidden="true"><circle cx="10" cy="10" r="9" fill="none" stroke="var(--teal)" stroke-width="2"/><path d="M7 5l2 3-1 1c1 2 2 3 4 4l1-1 3 2-1 2c-5 0-9-4-9-9z" fill="var(--teal)"/></svg>
      <span>555-014-2270</span>
    </li>
    <li>
      <svg viewBox="0 0 20 20" aria-hidden="true"><rect x="1" y="4" width="18" height="13" fill="var(--teal)"/><path d="M1 4l9 7 9-7" fill="none" stroke="#fff" stroke-width="1.5"/></svg>
      <span>mdovlatin@quorvane.studio</span>
    </li>
    <li>
      <svg viewBox="0 0 20 20" aria-hidden="true"><circle cx="10" cy="10" r="8.5" fill="none" stroke="var(--teal)" stroke-width="2"/><ellipse cx="10" cy="10" rx="3.5" ry="8.5" fill="none" stroke="var(--teal)" stroke-width="1.5"/><line x1="1.5" y1="10" x2="18.5" y2="10" stroke="var(--teal)" stroke-width="1.5"/></svg>
      <span>www.quorvane.studio</span>
    </li>
  </ul>
</section>

<section class="card card--back" aria-label="Card back">
  <h1 class="headline">How<br>can<br>we<br>help?</h1>

  <span class="services__spine" aria-hidden="true"></span>
  <ul class="services">
    <li class="service">
      <svg class="service__badge" viewBox="0 0 84 42" aria-hidden="true"><polygon points="42,1 83,21 42,41 1,21" fill="#fff" stroke="var(--ink)" stroke-width="1.5"/><rect x="36" y="12" width="12" height="18" rx="2" fill="none" stroke="var(--ink)" stroke-width="2"/></svg>
      <span class="service__label">Mobile learning SCORM</span>
    </li>
    <li class="service">
      <svg class="service__badge" viewBox="0 0 84 42" aria-hidden="true"><polygon points="42,1 83,21 42,41 1,21" fill="#fff" stroke="var(--ink)" stroke-width="1.5"/><rect x="33" y="13" width="18" height="14" fill="none" stroke="var(--ink)" stroke-width="2"/><line x1="36" y1="18" x2="48" y2="18" stroke="var(--ink)" stroke-width="1.5"/><line x1="36" y1="22" x2="45" y2="22" stroke="var(--ink)" stroke-width="1.5"/></svg>
      <span class="service__label">Instructional design LMS</span>
    </li>
    <li class="service">
      <svg class="service__badge" viewBox="0 0 84 42" aria-hidden="true"><polygon points="42,1 83,21 42,41 1,21" fill="#fff" stroke="var(--ink)" stroke-width="1.5"/><path d="M35 11h14l-2 16-5 3-5-3z" fill="none" stroke="var(--ink)" stroke-width="2"/></svg>
      <span class="service__label">MOOCs eLearning HTML5</span>
    </li>
    <li class="service">
      <svg class="service__badge" viewBox="0 0 84 42" aria-hidden="true"><polygon points="42,1 83,21 42,41 1,21" fill="#fff" stroke="var(--ink)" stroke-width="1.5"/><circle cx="42" cy="18" r="6" fill="var(--ink)"/><rect x="39" y="25" width="6" height="5" fill="var(--ink)"/></svg>
      <span class="service__label">Adult learning theory</span>
    </li>
    <li class="service">
      <svg class="service__badge" viewBox="0 0 84 42" aria-hidden="true"><polygon points="42,1 83,21 42,41 1,21" fill="#fff" stroke="var(--ink)" stroke-width="1.5"/><circle cx="42" cy="19" r="7" fill="none" stroke="var(--ink)" stroke-width="2"/><circle cx="42" cy="19" r="2.5" fill="var(--ink)"/></svg>
      <span class="service__label">Gamification classroom</span>
    </li>
    <li class="service">
      <svg class="service__badge" viewBox="0 0 84 42" aria-hidden="true"><polygon points="42,1 83,21 42,41 1,21" fill="#fff" stroke="var(--ink)" stroke-width="1.5"/><rect x="40" y="12" width="14" height="10" fill="none" stroke="var(--ink)" stroke-width="2"/><rect x="31" y="16" width="6" height="12" fill="var(--ink)"/><line x1="30" y1="29" x2="55" y2="29" stroke="var(--ink)" stroke-width="2"/></svg>
      <span class="service__label">xAPI blended learning</span>
    </li>
  </ul>
</section>

</body>
</html>
```